Brightwave Reach - Business Card

We need a business card for a Social Media Marketing company that specializes in online marketing for small businesses in Canada using common Social Media platforms such as Pixlora, Chatterly, Blinkpost & Quibber.

I have uploaded a copy of our logo which I would like utilized in the business card. We would like the business card to be modern yet classy design.

Our website is www.brightwavereach.ca

Industry/Entity Type

Marketing

Contact Information for Business Card

Email: info@brightwavereach.ca
Website: www.brightwavereach.ca
Telephone: 604-555-0193

Colors

Designer to choose colors to be used in the design.

Requirements
Must have
• Social Media icons on reverse
• Please add some designs with color.

```html
<!DOCTYPE html>
<html lang="en">
<head>
<meta charset="utf-8">
<title>Brightwave Reach – Business Card</title>
<link href="https://fonts.googleapis.com/css2?family=Roboto:wght@400;500;700&display=swap" rel="stylesheet">
<style>
  :root {
    --backdrop: #e4e4e4;
    --card-light: #f4f4f4;
    --card-dark: #3b3f42;
    --ink: #3a3d40;
    --ink-muted: #a8a8a8;
    --band-grey: #a9a9a9;
    --rule: #c9c9c9;
    --paper-text: #ffffff;
  }
  * { margin: 0; padding: 0; box-sizing: border-box; }
  html, body { width: 1200px; height: 960px; overflow: hidden; }
  body {
    background: var(--backdrop);
    font-family: "Roboto", Arial, sans-serif;
    color: var(--ink);
    position: relative;
  }
  .card { position: absolute; overflow: hidden; }

  /* Front */
  .card-front {
    left: 314px; top: 114px; width: 602px; height: 342px;
    background: var(--card-light);
  }
  .brand-name {
    position: absolute; left: 70px; top: 150px; width: 226px;
    text-align: center; font-weight: 700; font-size: 26px; line-height: 30px;
    color: var(--ink); text-transform: uppercase;
  }
  .divider {
    position: absolute; left: 306px; top: 86px; width: 1px; height: 156px;
    background: var(--rule);
  }
  .contact { position: absolute; left: 343px; top: 112px; }
  .person-name { font-size: 20px; font-weight: 500; letter-spacing: .2px; text-transform: uppercase; }
  .person-role { font-size: 14px; color: var(--ink-muted); margin-top: 3px; text-transform: uppercase; }
  .contact-list { list-style: none; margin-top: 22px; font-size: 14px; }
  .contact-list li { display: flex; align-items: center; height: 20px; }
  .contact-list svg { width: 12px; height: 12px; margin-right: 9px; fill: var(--ink); }
  .footer-bands { position: absolute; left: 0; bottom: 0; width: 602px; height: 36px; }
  .website {
    position: absolute; right: 30px; bottom: 11px;
    font-size: 14px; letter-spacing: 1.6px; color: var(--paper-text);
  }

  /* Back */
  .card-back {
    left: 311px; top: 472px; width: 601px; height: 343px;
    background: var(--card-dark);
  }
  .back-brand {
    position: absolute; left: 0; top: 140px; width: 100%;
    text-align: center; font-weight: 700; font-size: 34px; line-height: 40px;
    color: var(--paper-text); text-transform: uppercase;
  }
  .social-row {
    position: absolute; left: 124px; top: 288px; width: 356px;
    display: flex; align-items: center; gap: 10px;
  }
  .social-row .line { flex: 1; height: 1px; background: #8a8d90; }
  .social-list { list-style: none; display: flex; gap: 10px; }
  .social-list li { font-size: 12px; color: var(--paper-text); letter-spacing: .4px; }
</style>
</head>
<body>

<section class="card card-front" aria-label="Card front">
  <div class="brand-name">Brightwave<br>Reach</div>

  <div class="divider"></div>

  <div class="contact">
    <p class="person-name">Alex Morgan</p>
    <p class="person-role">CEO/Founder</p>
    <ul class="contact-list">
      <li>
        <svg viewBox="0 0 24 24" aria-hidden="true"><path d="M6.6 10.8a15.1 15.1 0 0 0 6.6 6.6l2.2-2.2c.3-.3.7-.4 1-.2 1.1.4 2.3.6 3.6.6.6 0 1 .4 1 1V20c0 .6-.4 1-1 1A17 17 0 0 1 3 4c0-.6.4-1 1-1h3.5c.6 0 1 .4 1 1 0 1.3.2 2.5.6 3.6.1.3 0 .7-.2 1z"/></svg>
        604-555-0193
      </li>
      <li>
        <svg viewBox="0 0 24 24" aria-hidden="true"><path d="M2 5h20v14H2z"/><path d="M3 6l9 7 9-7" fill="none" stroke="var(--card-light)" stroke-width="2"/></svg>
        info@brightwavereach.ca
      </li>
    </ul>
  </div>

  <svg class="footer-bands" viewBox="0 0 602 36" aria-hidden="true">
    <polygon points="0,16 352,16 344,27 0,27" fill="var(--band-grey)"/>
    <polygon points="369,6 602,6 602,36 0,36 0,27 344,27" fill="var(--card-dark)"/>
  </svg>
  <p class="website">www.brightwavereach.ca</p>
</section>

<section class="card card-back" aria-label="Card back">
  <div class="back-brand">Brightwave Reach</div>
  <div class="social-row">
    <span class="line"></span>
    <ul class="social-list">
      <li>Chatterly</li>
      <li>Pixlora</li>
      <li>Quibber</li>
    </ul>
    <span class="line"></span>
  </div>
</section>

</body>
</html>
```